Marlow Estate Fixers (Handyman / Home Improvement Company)

Looking for a double sided professional looking business card with Logo attached to be highlighted on one side and throwing in an image of a handyman as an option would be nice to see as well. We are a company focused on providing quality Handyman and Home improvement services in a timely manner that is done right the first time with integrity

Industry/Entity Type

Handyman / Home Improvement

Contact Information for Business Card

(LOGO, Name, Mobile and office phone numbers, email) on front side of card, (the words "The SOLUTION to all of your Handyman and Home Improvement needs" followed by "Family Owned and Operated" at the very bottom) on the back.

Colors
EB3D1F
EC4F4E
F09395
F8D3D4
FCEDEE

Requirements
Must have
• Red, Gray, Black Color scheme
Should not have
• No Yellow or Blue colors

```html
<!DOCTYPE html>
<html lang="en">
<head>
<meta charset="utf-8">
<title>Marlow Estate Fixers – Business Card</title>
<link rel="stylesheet" href="https://fonts.googleapis.com/css2?family=Lato:ital,wght@0,400;0,700;0,900;1,400&display=swap">
<style>
  :root {
    --red: #e5202e;
    --black: #1a1a1a;
    --card-dark: #1c1c1c;
    --white: #ffffff;
    --grey-text: #2b2b2b;
    --faint-grey: #ececec;
    --faint-red: #fcedee;
    --stage: #3a3d3e;
  }
  * { box-sizing: border-box; margin: 0; padding: 0; }
  html, body { width: 1200px; height: 1122px; overflow: hidden; }
  body {
    background: var(--stage);
    font-family: "Lato", sans-serif;
    position: relative;
  }
  .card {
    position: absolute;
    width: 640px;
    height: 366px;
    border-radius: 22px;
    overflow: hidden;
    box-shadow: 0 14px 30px rgba(0,0,0,.45);
  }

  /* Back side */
  .card--back {
    left: 80px; top: 130px;
    background: var(--card-dark);
    color: var(--white);
    display: flex;
    flex-direction: column;
    align-items: center;
    justify-content: center;
    text-align: center;
  }
  .brand {
    display: flex;
    align-items: center;
    gap: 14px;
    font-weight: 900;
    text-transform: uppercase;
    letter-spacing: .04em;
  }
  .brand__dot { border-radius: 50%; flex: none; }
  .card--back .brand { font-size: 34px; color: #8a8a8a; margin-bottom: 40px; }
  .card--back .brand__dot { width: 34px; height: 34px; background: #8a8a8a; }
  .tagline {
    font-weight: 900;
    font-size: 22px;
    line-height: 1.25;
    text-transform: uppercase;
    letter-spacing: .01em;
  }
  .tagline em { font-style: normal; color: var(--red); }
  .family {
    margin-top: 10px;
    font-size: 17px;
    color: var(--red);
    font-weight: 400;
  }

  /* Front side */
  .card--front {
    left: 480px; top: 620px;
    background: var(--white);
  }
  .watermark {
    position: absolute;
    left: 60px; top: 120px;
    width: 380px; height: 380px;
    border-radius: 50%;
    background: var(--faint-grey);
    opacity: .7;
  }
  .card--front .brand {
    position: absolute;
    right: 40px; top: 40px;
    font-size: 24px;
    color: var(--red);
  }
  .card--front .brand__dot { width: 26px; height: 26px; background: var(--black); }
  .divider {
    position: absolute;
    left: 300px; right: 0; top: 202px;
    height: 3px;
    background: var(--black);
  }
  .person {
    position: absolute;
    left: 48px; top: 150px;
  }
  .person__name {
    font-size: 34px;
    font-weight: 900;
    color: var(--red);
    text-transform: uppercase;
    letter-spacing: .02em;
    line-height: 1;
  }
  .person__role {
    font-size: 19px;
    color: var(--grey-text);
    margin-top: 8px;
  }
  .person__rule {
    width: 200px; height: 3px;
    background: var(--red);
    margin-top: 10px;
  }
  .contact {
    position: absolute;
    left: 60px; top: 256px;
    list-style: none;
    font-size: 18px;
    color: var(--grey-text);
  }
  .contact li {
    display: flex;
    align-items: center;
    gap: 14px;
    height: 30px;
  }
  .contact svg { width: 18px; height: 18px; flex: none; }
</style>
</head>
<body>

  <section class="card card--back" aria-label="Business card back">
    <div class="brand"><span class="brand__dot"></span>Marlow Estate Fixers</div>
    <p class="tagline">Your <em>Solution</em> to all of your<br>Handyman &amp; Home Improvement Needs</p>
    <p class="family">Family Owned &amp; Operated</p>
  </section>

  <section class="card card--front" aria-label="Business card front">
    <div class="watermark"></div>
    <div class="brand"><span class="brand__dot"></span>Marlow Estate Fixers</div>
    <div class="divider"></div>

    <div class="person">
      <h1 class="person__name">Daniel Harrow</h1>
      <p class="person__role">Founder &amp; CEO</p>
      <div class="person__rule"></div>
    </div>

    <ul class="contact">
      <li>
        <svg viewBox="0 0 24 24" aria-hidden="true"><path fill="#e5202e" d="M6.6 10.8a15.2 15.2 0 0 0 6.6 6.6l2.2-2.2a1 1 0 0 1 1-.25 11.4 11.4 0 0 0 3.6.57 1 1 0 0 1 1 1V20a1 1 0 0 1-1 1A17 17 0 0 1 3 4a1 1 0 0 1 1-1h3.5a1 1 0 0 1 1 1c0 1.25.2 2.45.57 3.57a1 1 0 0 1-.25 1z"/></svg>
        (123) 456-7890
      </li>
      <li>
        <svg viewBox="0 0 24 24" aria-hidden="true"><rect x="6" y="2" width="12" height="20" rx="2.5" fill="none" stroke="#e5202e" stroke-width="2.2"/><circle cx="12" cy="18" r="1.3" fill="#e5202e"/></svg>
        (123) 456-7890
      </li>
      <li>
        <svg viewBox="0 0 24 24" aria-hidden="true"><rect x="2" y="5" width="20" height="14" rx="1.5" fill="#e5202e"/><path d="M3 6l9 7 9-7" fill="none" stroke="#fff" stroke-width="1.6"/></svg>
        info@yourwebsitehere.com
      </li>
    </ul>
  </section>

</body>
</html>
```